Social Media App Needs PPT Template

We need a PowerPoint template for a new social media company based in the DC area called "Bold Ledger." We provide an interactive digital platform for executives to share actionable advice. We would like to see designs that use our orange logo color as an accent, but are mainly grey, white, and black. The final design should communicate clean, chic, modern, and professional.

Target Market(s)

Executives

Industry/Entity Type

Information Technology

Font styles to use
Sans Serif

Colors
f78f20
fbe7d2
ffffff
000000
e8e8e8
757575

Requirements
Must have
• My project must have title page and many options for the body of the ppt (graphs, tables, etc). It also needs to be easy to modify. I must have someone who is experienced in creating powerpoint templates.
Nice to have
• It would be nice to have a very modern and clean design that includes the logo on every page, but still leaves a lot of room for the content of the slide
Should not have
• My design project should not look to busy.

```html
<!DOCTYPE html>
<html lang="en">
<head>
<meta charset="utf-8">
<title>Bold Ledger – Chart Slide</title>
<link href="https://fonts.googleapis.com/css2?family=Bebas+Neue&family=Lato:wght@300;400;700&display=swap" rel="stylesheet">
<style>
  :root {
    --backdrop: #545454;
    --paper: #ffffff;
    --accent: #f39320;
    --navy: #222d3b;
    --grey: #6d6e70;
    --text: #555555;
    --axis: #8a8a8a;
    --soft: #eeeeee;
  }
  * { margin: 0; padding: 0; box-sizing: border-box; }
  html, body {
    width: 1200px; height: 960px; overflow: hidden;
    background: var(--backdrop);
    font-family: "Lato", Arial, sans-serif;
  }
  .page-label {
    position: absolute; top: 74px; left: 0; width: 1200px;
    text-align: center; color: var(--soft);
    font-weight: 300; font-size: 27px;
  }
  .slide {
    position: absolute; left: 123px; top: 159px;
    width: 987px; height: 741px; background: var(--paper);
  }
  .accent-band {
    position: absolute; left: 0; top: 15px; width: 100%; height: 11px;
    background: var(--accent);
  }
  .title-band {
    position: absolute; left: 0; top: 29px; width: 100%; height: 95px;
    background: var(--navy);
  }
  .slide-title {
    position: absolute; left: 42px; top: 50%; transform: translateY(-46%);
    font-family: "Bebas Neue", "Arial Narrow", sans-serif;
    font-size: 56px; font-weight: 400; color: var(--paper);
    letter-spacing: -0.5px; line-height: 1;
  }
  .brand {
    position: absolute; right: 38px; top: 50%; transform: translateY(-50%);
    display: flex; align-items: center; gap: 10px;
    font-weight: 700; font-size: 26px; color: var(--paper);
  }
  .brand-dot {
    width: 14px; height: 14px; border-radius: 50%; background: var(--accent);
  }
  .chart { position: absolute; left: 0; top: 0; }
  .chart text { font-family: "Lato", Arial, sans-serif; fill: var(--text); }
  .body-copy {
    position: absolute; left: 51px; top: 528px; width: 895px;
    font-size: 17px; line-height: 25px; color: var(--text);
    text-align: justify;
  }
  .footer-rule {
    position: absolute; left: 663px; top: 684px; width: 287px;
    border-top: 1px solid var(--grey);
  }
  .footer-note {
    position: absolute; right: 35px; top: 703px;
    font-size: 13px; color: var(--grey);
  }
</style>
</head>
<body>
  <div class="page-label">Page 6</div>

  <section class="slide">
    <div class="accent-band"></div>
    <header class="title-band">
      <h1 class="slide-title">Title Goes Here</h1>
      <div class="brand"><span class="brand-dot"></span>Bold Ledger</div>
    </header>

    <svg class="chart" width="987" height="520" viewBox="0 0 987 520" aria-label="Bar chart of three series across three categories">
      <g stroke="var(--axis)" stroke-width="1" stroke-dasharray="8 6">
        <line x1="81" y1="203" x2="817" y2="203"/>
        <line x1="81" y1="255" x2="817" y2="255"/>
        <line x1="81" y1="303" x2="817" y2="303"/>
        <line x1="81" y1="351" x2="817" y2="351"/>
        <line x1="81" y1="403" x2="817" y2="403"/>
      </g>
      <g>
        <rect x="122" y="239" width="48" height="212" fill="var(--accent)"/>
        <rect x="170" y="282" width="48" height="169" fill="var(--navy)"/>
        <rect x="218" y="256" width="48" height="195" fill="var(--grey)"/>
        <rect x="349" y="269" width="48" height="182" fill="var(--accent)"/>
        <rect x="397" y="236" width="48" height="215" fill="var(--navy)"/>
        <rect x="445" y="283" width="48" height="168" fill="var(--grey)"/>
        <rect x="568" y="297" width="48" height="154" fill="var(--accent)"/>
        <rect x="616" y="250" width="48" height="201" fill="var(--navy)"/>
        <rect x="664" y="232" width="48" height="219" fill="var(--grey)"/>
      </g>
      <g stroke="var(--axis)" stroke-width="1">
        <line x1="81.5" y1="203" x2="81.5" y2="455"/>
        <line x1="77" y1="451.5" x2="815" y2="451.5"/>
      </g>
      <g font-size="16" text-anchor="middle" dominant-baseline="middle">
        <text x="59" y="207">5</text>
        <text x="59" y="258">4</text>
        <text x="59" y="305">3</text>
        <text x="59" y="355">2</text>
        <text x="59" y="403">1</text>
        <text x="59" y="455">0</text>
      </g>
      <g font-size="17" text-anchor="middle" dominant-baseline="middle">
        <text x="190" y="479">Category 1</text>
        <text x="417" y="479">Category 2</text>
        <text x="644" y="479">Category 3</text>
      </g>
      <g font-size="19" dominant-baseline="middle">
        <rect x="866" y="198" width="10" height="10" fill="var(--accent)"/>
        <text x="880" y="204">Series 1</text>
        <rect x="866" y="224" width="10" height="10" fill="var(--navy)"/>
        <text x="880" y="230">Series 2</text>
        <rect x="866" y="251" width="10" height="10" fill="var(--grey)"/>
        <text x="880" y="257">Series 3</text>
      </g>
    </svg>

    <p class="body-copy">Duis autem vel eum iriure dolor in hendrerit in vulputate velit esse molestie consequat, vel illum dolore eu feugiat nulla facilisis at vero eros et accumsan et iusto odio dignissim qui blandit praesent luptatum zzril delenit augue duis dolore te feugait nulla facilisi. Nam liber tempor cum soluta nobis eleifend option congue nihil imperdiet doming id quod mazim placerat facer possim assum.</p>

    <div class="footer-rule"></div>
    <div class="footer-note">www.boldledger.com &nbsp;|&nbsp; Page 4</div>
  </section>
</body>
</html>
```